Stylish Business Cards Wanted

- DOUBLE SIDED Design Required -

High end, edgy cards for a corporate and personal stylist. Must include logo,
Name: Belinda Harwick
Title: Director and Stylist
telephone : +61 8 7142 5809
email: belinda@theloombriefing.example
website: theloombriefing.example
Tag: Corporate Workwear & Uniform Specialist | Personal Stylist
Would like nice icons for telephone, email, website

Target Market(s)

Businesses wanting stylish uniforms, people wanting stylish wardrobes

Industry/Entity Type

Corporate Workwear Stylist

Contact Information for Business Card

I would like black, white and gold foiling incorporated in the design - possibly a touch of the other colours on my branding guide attached Name: Belinda Harwick Title: Director and Stylist telephone : +61 8 7142 5809 email: belinda@theloombriefing.example website: theloombriefing.example Tag: Corporate Workwear & Uniform Specialist | Personal Stylist Would like nice icons for telephone, email, website

Font styles to use
Other font styles liked:
• Raleway

Colors

Designer to choose colors to be used in the design.

Requirements
Must have
• Gold foil accents

```html
<!DOCTYPE html>
<html lang="en">
<head>
<meta charset="utf-8">
<title>The Loom Briefing – Business Cards</title>
<link href="https://fonts.googleapis.com/css2?family=Open+Sans:wght@400;600;700&display=swap" rel="stylesheet">
<style>
  :root {
    --backdrop: #2a2a2a;
    --card: #151515;
    --gold: #d9cc8a;
    --gold-deep: #b8a865;
    --gold-edge: #e6dca3;
  }
  * { box-sizing: border-box; margin: 0; padding: 0; }
  html, body { width: 1200px; height: 900px; overflow: hidden; }
  body {
    background: var(--backdrop);
    font-family: "Open Sans", Arial, sans-serif;
    color: var(--gold);
    position: relative;
  }
  .card {
    position: absolute;
    left: 250px;
    width: 700px;
    height: 400px;
    background: var(--card);
    box-shadow: 0 14px 30px rgba(0,0,0,0.55);
    overflow: hidden;
  }
  .card::after {
    content: "";
    position: absolute;
    left: 0; right: 0; bottom: 0;
    height: 6px;
    background: linear-gradient(90deg, var(--gold-deep), var(--gold-edge), var(--gold-deep));
  }
  .card--back { top: 40px; }
  .card--front { top: 470px; }

  /* Back */
  .brand-name {
    font-weight: 700;
    color: var(--gold);
    letter-spacing: 0.04em;
    white-space: nowrap;
  }
  .card--back .brand {
    position: absolute;
    right: 70px;
    top: 110px;
    display: flex;
    align-items: center;
    gap: 18px;
  }
  .card--back .brand-name { font-size: 52px; }
  .brand-mark {
    width: 22px; height: 22px;
    border-radius: 50%;
    background: var(--gold);
    flex: none;
  }
  .tagline {
    position: absolute;
    left: 60px;
    bottom: 50px;
    font-size: 19px;
    font-weight: 400;
    letter-spacing: 0.01em;
  }
  .tagline .dot { margin: 0 12px; }

  /* Front */
  .card--front .brand {
    position: absolute;
    left: 40px;
    top: 163px;
    width: 290px;
    display: flex;
    align-items: center;
    gap: 10px;
  }
  .card--front .brand-name { font-size: 24px; }
  .card--front .brand-mark { width: 12px; height: 12px; }
  .divider {
    position: absolute;
    left: 355px;
    top: 90px;
    width: 1px;
    height: 220px;
    background: var(--gold-deep);
  }
  .contact-block {
    position: absolute;
    left: 382px;
    top: 100px;
    right: 12px;
  }
  .person-name {
    font-size: 27px;
    font-weight: 700;
    letter-spacing: 0.04em;
    text-transform: uppercase;
    white-space: nowrap;
  }
  .person-title {
    font-size: 18px;
    margin-top: 4px;
  }
  .contact-list { list-style: none; margin-top: 34px; }
  .contact-list li {
    display: flex;
    align-items: center;
    gap: 10px;
    font-size: 17px;
    line-height: 1.75;
    white-space: nowrap;
  }
  .contact-list svg { width: 16px; height: 16px; flex: none; }
</style>
</head>
<body>

  <section class="card card--back" aria-label="Business card back">
    <div class="brand">
      <span class="brand-mark"></span>
      <span class="brand-name">The Loom Briefing</span>
    </div>
    <p class="tagline">Corporate Workwear &amp; Uniform Specialist<span class="dot">•</span>Personal Stylist</p>
  </section>

  <section class="card card--front" aria-label="Business card front">
    <div class="brand">
      <span class="brand-mark"></span>
      <span class="brand-name">The Loom Briefing</span>
    </div>
    <div class="divider"></div>
    <div class="contact-block">
      <h1 class="person-name">Belinda Harwick</h1>
      <p class="person-title">Director and Stylist</p>
      <ul class="contact-list">
        <li>
          <svg viewBox="0 0 16 16" aria-hidden="true"><circle cx="8" cy="8" r="8" fill="var(--gold)"/><path d="M5.2 4.2l1.4 0 .6 1.8-.9.7a5 5 0 0 0 2.9 2.9l.7-.9 1.8.6 0 1.4c-3.6.4-6.9-2.9-6.5-6.5z" fill="var(--card)"/></svg>
          +61 8 7142 5809
        </li>
        <li>
          <svg viewBox="0 0 16 16" aria-hidden="true"><rect x="1" y="3.5" width="14" height="9" rx="1" fill="var(--gold)"/><path d="M1.5 4.2L8 9l6.5-4.8" fill="none" stroke="var(--card)" stroke-width="1.2"/></svg>
          belinda@theloombriefing.example
        </li>
        <li>
          <svg viewBox="0 0 16 16" aria-hidden="true"><circle cx="8" cy="8" r="7" fill="none" stroke="var(--gold)" stroke-width="1.4"/><ellipse cx="8" cy="8" rx="3" ry="7" fill="none" stroke="var(--gold)" stroke-width="1.2"/><path d="M1 8h14" stroke="var(--gold)" stroke-width="1.2"/></svg>
          theloombriefing.example
        </li>
      </ul>
    </div>
  </section>

</body>
</html>
```